New Business Card Design Project

Need a design that will create an impact / strong impression towards our clients for our business. We are in the lighting business and we do lighting retrofits for large commercial to industrial clientele.

Target Market(s)

Lighting Industry

Industry/Entity Type

Business

Font styles to use
Other font styles liked:
• we would like to use the font on our logo, not sure what it is though..

Requirements
Must have
• Our logo.
Nice to have
• We are open to suggestions that have to do with lighting.

```html
<!DOCTYPE html>
<html lang="en">
<head>
<meta charset="utf-8">
<title>Lumenworks Group – Business Card</title>
<link rel="stylesheet" href="https://fonts.googleapis.com/css2?family=Lato:wght@400;700&display=swap">
<style>
  :root {
    --page-bg: #ececec;
    --card-white: #ffffff;
    --green: #0e8040;
    --green-light: #6cc04a;
    --green-dark: #1e3d20;
    --green-deep: #18321a;
    --ink-grey: #6b6b6b;
    --text-white: #ffffff;
  }
  * { box-sizing: border-box; margin: 0; padding: 0; }
  html, body {
    width: 1200px; height: 1000px; overflow: hidden;
    background: var(--page-bg);
    font-family: "Lato", sans-serif;
  }
  .canvas { position: relative; width: 1200px; height: 1000px; }
  .card {
    position: absolute; left: 240px; width: 697px;
    border-radius: 20px; overflow: hidden;
  }
  .card-front { top: 83px; height: 395px; background: var(--card-white); }
  .card-back {
    top: 520px; height: 397px;
    background: linear-gradient(135deg, var(--green-deep) 0%, var(--green-dark) 55%, #22482a 100%);
  }
  .brand {
    position: absolute; display: flex; align-items: center; gap: 10px;
    font-weight: 700; white-space: nowrap; line-height: 1.2;
  }
  .brand-square { width: 16px; height: 16px; flex: none; }
  .card-front .brand {
    left: 53px; top: 180px; width: 280px;
    font-size: 27px; color: var(--green-dark);
  }
  .card-front .brand-square { background: var(--green); }
  .divider {
    position: absolute; left: 363px; top: 134px;
    width: 2px; height: 130px; background: var(--green);
  }
  .person { position: absolute; left: 400px; top: 133px; }
  .person-name { font-size: 21px; font-weight: 700; color: var(--green); letter-spacing: 0.5px; }
  .person-role { font-size: 17px; color: var(--ink-grey); margin-top: 1px; }
  .contact-list { list-style: none; margin-top: 16px; }
  .contact-item {
    display: flex; align-items: center; gap: 12px;
    font-size: 15px; color: var(--ink-grey); height: 22.5px; letter-spacing: 0.3px;
  }
  .contact-icon { width: 12px; height: 12px; fill: var(--green); flex: none; margin-left: 3px; }
  .address-rule {
    position: absolute; left: 0; top: 345px; width: 100%; height: 4px; background: var(--green-light);
  }
  .address-band {
    position: absolute; left: 0; top: 351px; width: 100%; height: 44px;
    background: var(--green); color: var(--text-white);
    display: flex; align-items: center; justify-content: center;
    font-size: 15px; letter-spacing: 0.8px;
  }
  .card-back .brand {
    left: 0; right: 0; justify-content: center; top: 160px;
    font-size: 44px; color: var(--text-white); gap: 12px;
  }
  .card-back .brand-square { background: var(--green-light); width: 22px; height: 22px; }
  .back-web {
    position: absolute; left: 0; right: 0; top: 353px; text-align: center;
    font-size: 14px; color: var(--text-white); letter-spacing: 1.5px;
  }
</style>
</head>
<body>
<main class="canvas">
  <section class="card card-front">
    <div class="brand"><span class="brand-square"></span>Lumenworks Group</div>
    <div class="divider"></div>
    <div class="person">
      <p class="person-name">DANIEL HARPER</p>
      <p class="person-role">Founder</p>
      <ul class="contact-list">
        <li class="contact-item">
          <svg class="contact-icon" viewBox="0 0 24 24"><path d="M6.6 10.8a15 15 0 0 0 6.6 6.6l2.2-2.2a1 1 0 0 1 1-.25 11.4 11.4 0 0 0 3.6.6 1 1 0 0 1 1 1V20a1 1 0 0 1-1 1A17 17 0 0 1 3 4a1 1 0 0 1 1-1h3.5a1 1 0 0 1 1 1c0 1.25.2 2.45.6 3.6a1 1 0 0 1-.25 1z"/></svg>
          0400 555 019
        </li>
        <li class="contact-item">
          <svg class="contact-icon" viewBox="0 0 24 24"><path d="M2 5h20v14H2z"/><path d="M2 5l10 8 10-8" stroke="#fff" stroke-width="2" fill="none"/></svg>
          hello@lumenworksgroup.com
        </li>
        <li class="contact-item">
          <svg class="contact-icon" viewBox="0 0 24 24"><circle cx="12" cy="12" r="10"/><path d="M2 12h20M12 2c3 3 3 17 0 20M12 2c-3 3-3 17 0 20" stroke="#fff" stroke-width="1.5" fill="none"/></svg>
          www.lumenworksgroup.com
        </li>
      </ul>
    </div>
    <div class="address-rule"></div>
    <div class="address-band">4870 West Canyon Road, Suite C204 Tempe AZ 85281</div>
  </section>

  <section class="card card-back">
    <div class="brand"><span class="brand-square"></span>Lumenworks Group</div>
    <p class="back-web">www.lumenworksgroup.com</p>
  </section>
</main>
</body>
</html>
```